Quillmarsh Capital LLC

Need Professional Business cards for New Investment Fund

Target Market(s)

High Quality investors

Industry/Entity Type

Financial

Contact Information for Business Card

Phone Number +1 555 284 6190
Name Lukas Varenko
Title Fund Manager
email lv@FundQuillmarsh.com
Website www.FundQuillmarsh.com

Colors

Designer to choose colors to be used in the design.

Requirements
Must have
• Must have our Logo and all of the above. Must be made so lettering and loge can be raised

```html
<!DOCTYPE html>
<html lang="en">
<head>
<meta charset="UTF-8">
<title>Quillmarsh Capital LLC — Business Card</title>
<link rel="stylesheet" href="https://fonts.googleapis.com/css2?family=Oswald:wght@500&family=Raleway:wght@400;500;600&display=swap">
<style>
  :root {
    --backdrop: #1f1f1f;
    --card: #434e42;
    --accent: #5bbf47;
    --ink: #ffffff;
    --ink-soft: #e8ece7;
  }
  * { box-sizing: border-box; margin: 0; padding: 0; }
  html, body { width: 1200px; height: 900px; overflow: hidden; }
  body {
    background: var(--backdrop);
    display: flex;
    flex-direction: column;
    align-items: center;
    justify-content: center;
    gap: 40px;
    font-family: "Raleway", sans-serif;
  }
  .card {
    position: relative;
    width: 660px;
    height: 377px;
    background: var(--card);
    box-shadow: 0 14px 30px rgba(0,0,0,0.5);
    overflow: hidden;
  }

  /* Front */
  .brand {
    position: absolute;
    left: 52%;
    top: 46%;
    transform: translate(-50%, -50%);
    display: flex;
    align-items: center;
    gap: 12px;
    white-space: nowrap;
  }
  .brand-mark {
    width: 22px;
    height: 22px;
    background: var(--accent);
  }
  .brand-name {
    font-weight: 600;
    font-size: 32px;
    letter-spacing: 3px;
    color: var(--ink);
  }
  .front-bar {
    position: absolute;
    bottom: 0;
    left: 33%;
    width: 29%;
    height: 9px;
    background: var(--accent);
  }

  /* Back */
  .identity {
    position: absolute;
    right: 392px;
    bottom: 56px;
    text-align: right;
    white-space: nowrap;
  }
  .person-name {
    font-family: "Oswald", sans-serif;
    font-weight: 500;
    font-size: 32px;
    line-height: 1.05;
    text-transform: uppercase;
    color: var(--ink);
    letter-spacing: 0.5px;
  }
  .person-title {
    font-size: 20px;
    color: var(--ink-soft);
    margin-top: 2px;
  }
  .divider {
    position: absolute;
    left: 282px;
    bottom: 34px;
    width: 2px;
    height: 94px;
    background: var(--accent);
  }
  .contacts {
    position: absolute;
    left: 298px;
    bottom: 30px;
    list-style: none;
    white-space: nowrap;
  }
  .contacts li {
    display: flex;
    align-items: center;
    gap: 12px;
    font-size: 20px;
    color: var(--ink);
    line-height: 1.5;
  }
  .contacts svg { width: 16px; height: 16px; flex: none; }
  .back-bar-accent {
    position: absolute;
    bottom: 0;
    left: 0;
    width: 40%;
    height: 9px;
    background: var(--accent);
  }
  .back-bar-light {
    position: absolute;
    bottom: 0;
    left: 41%;
    right: 0;
    height: 9px;
    background: var(--ink);
  }
</style>
</head>
<body>
  <section class="card card-front" aria-label="Card front">
    <div class="brand">
      <span class="brand-mark"></span>
      <span class="brand-name">QUILLMARSH</span>
    </div>
    <div class="front-bar"></div>
  </section>

  <section class="card card-back" aria-label="Card back">
    <div class="identity">
      <p class="person-name">Lukas Varenko</p>
      <p class="person-title">Title Fund Manager</p>
    </div>
    <div class="divider"></div>
    <ul class="contacts">
      <li>
        <svg viewBox="0 0 16 16" aria-hidden="true"><path d="M3.5 1.5l2.5 0 1 3.5-1.6 1.1c.8 1.8 2.2 3.2 4 4l1.1-1.6 3.5 1v2.5c0 .8-.7 1.5-1.5 1.5C7 13.5 2 8.5 2 3c0-.8.7-1.5 1.5-1.5z" fill="var(--accent)"/></svg>
        +1 555 284 6190
      </li>
      <li>
        <svg viewBox="0 0 16 16" aria-hidden="true"><rect x="1.5" y="3.5" width="13" height="9" fill="none" stroke="var(--accent)" stroke-width="1.4"/><path d="M1.5 3.5L8 9l6.5-5.5" fill="none" stroke="var(--accent)" stroke-width="1.4"/></svg>
        lv@FundQuillmarsh.com
      </li>
      <li>
        <svg viewBox="0 0 16 16" aria-hidden="true"><g fill="none" stroke="var(--accent)" stroke-width="1.2"><circle cx="8" cy="8" r="6.3"/><ellipse cx="8" cy="8" rx="2.8" ry="6.3"/><path d="M1.7 8h12.6M2.6 5h10.8M2.6 11h10.8"/></g></svg>
        www.FundQuillmarsh.com
      </li>
    </ul>
    <div class="back-bar-accent"></div>
    <div class="back-bar-light"></div>
  </section>
</body>
</html>
```